Church needs a street sign design

We're a small church located in Silicon Valley, California. Our website is https://www.vgtmarlowfield.org/ and our address is 4817 Ferrow Ave, San Jose, California, 95873. You can look up our location on Google Maps to see the sign from Street View. I have uploaded an image of the street sign as well. The marquee, the top section of the sign, and the separating line between them both will be removed. We're seeking a design for a new backlit acrylic insert that will go on the front of the light box and the back of the lightbox. The acrylic sign will fill the entire external frame. In the future, we may build a decorative wood frame around the structural legs, as visualized in one of the uploaded files. The church's brand colors are: #003366 (dark blue), #ff6600 (vibrant orange), #228b22 (forest green). I have also uploaded the church's logo assets. Our primary font is Montserrat and the secondary is Poppins. You can deviate from these colors/fonts if the sign is still coherent with the rest of our branding. Our branding values are mission, truth, passion, and community (please do not put those words on the sign! They are just intended to guide the look of the design). The sign dimensions are 96" by 47.5". Keep in mind that the sign will be backlit on a busy street side. It will also be positioned next to an old-looking church building. We do NOT want a sign that looks traditional, old, or antiquated. Instead, we want a modern-looking sign that pairs well with our old building while helping it look more modern too. We would also like the web address clearly visible on the sign: vgtmarlowfield.org. If you have any questions, just let me know!

```html
<!DOCTYPE html>
<html lang="en">
<head>
<meta charset="UTF-8">
<title>Marlowfield Grace Church – Street Sign Insert</title>
<link href="https://fonts.googleapis.com/css2?family=Montserrat:wght@600;800&family=Mrs+Saint+Delafield&display=swap" rel="stylesheet">
<style>
  :root {
    --navy: #101a45;
    --navy-deep: #0c1438;
    --royal: #1a3fa8;
    --sky: #4fb6f7;
    --orange: #ff6600;
    --cream: #fff4ec;
    --white: #ffffff;
    --page: #ffffff;
  }
  * { margin: 0; padding: 0; box-sizing: border-box; }
  html, body {
    width: 1200px; height: 905px; overflow: hidden;
    background: var(--page);
  }
  .sign {
    position: absolute; left: 112px; top: 212px;
    width: 976px; height: 485px; overflow: hidden;
    background:
      radial-gradient(ellipse 420px 260px at 520px 360px, rgba(40,100,220,.55), transparent 70%),
      radial-gradient(ellipse 380px 220px at 820px 420px, rgba(30,70,190,.45), transparent 70%),
      var(--navy);
    box-shadow: 10px 10px 8px rgba(0,0,0,.35);
    font-family: 'Montserrat', sans-serif;
  }
  .sign__art { position: absolute; inset: 0; }
  .headline {
    position: absolute; left: 58px; top: 52px;
    color: var(--white); font-weight: 800;
    font-size: 71px; line-height: 61px; letter-spacing: -1px;
  }
  .subline {
    position: absolute; left: 59px; top: 192px;
    color: var(--sky); font-weight: 800;
    font-size: 36px; line-height: 37px;
  }
  .tagline {
    position: absolute; left: 56px; top: 284px;
    color: var(--white);
    font-family: 'Mrs Saint Delafield', cursive;
    font-size: 50px; line-height: 1; white-space: nowrap;
  }
  .web-band {
    position: absolute; left: 0; top: 366px;
    width: 604px; height: 70px;
    background: var(--orange);
    clip-path: polygon(0 0, 100% 0, 94.5% 100%, 0 100%);
  }
  .web-band__url {
    position: absolute; left: 57px; top: 9px;
    color: var(--cream); font-weight: 800;
    font-size: 43px; line-height: 50px; letter-spacing: .5px;
    text-shadow: 2px 2px 3px rgba(0,0,0,.25);
  }
  .church-name {
    position: absolute; left: 655px; top: 336px;
    display: flex; align-items: center; gap: 16px;
    color: var(--white); font-weight: 600;
  }
  .church-name__mark {
    width: 52px; height: 52px; border: 4px solid var(--white);
  }
  .church-name__text { line-height: 1.15; }
  .church-name__main { display: block; font-size: 27px; }
  .church-name__sub { display: block; font-size: 15px; letter-spacing: 1px; }
</style>
</head>
<body>
  <main class="sign">
    <svg class="sign__art" width="976" height="485" viewBox="0 0 976 485">
      <defs>
        <linearGradient id="sky-wedge" x1="0" y1="0" x2="0" y2="1">
          <stop offset="0" stop-color="#57c2ff"/>
          <stop offset="1" stop-color="#1f5fd0"/>
        </linearGradient>
        <linearGradient id="coast-photo" x1="0" y1="0" x2="0" y2="1">
          <stop offset="0" stop-color="#d9a08f"/>
          <stop offset=".12" stop-color="#8a8aa6"/>
          <stop offset=".3" stop-color="#c7a78a"/>
          <stop offset=".6" stop-color="#6b5a62"/>
          <stop offset="1" stop-color="#4a4650"/>
        </linearGradient>
      </defs>
      <polygon points="440,0 560,0 498,112" fill="#1c3a9e"/>
      <polygon points="447,0 557,0 503,107" fill="url(#sky-wedge)"/>
      <polygon points="556,0 976,0 824,310 406,310" fill="url(#coast-photo)"
               role="img" aria-label="Aerial photo of a coastal boulevard with palm trees, beach and pier at sunset"/>
    </svg>

    <h1 class="headline">MAKING<br>DISCIPLES</h1>
    <p class="subline">&amp; HELPING THE<br>HELPLESS</p>
    <p class="tagline">For the Glory of Christ</p>

    <div class="web-band">
      <span class="web-band__url">vgtmarlowfield.org</span>
    </div>

    <div class="church-name">
      <span class="church-name__mark"></span>
      <span class="church-name__text">
        <span class="church-name__main">MARLOWFIELD</span>
        <span class="church-name__sub">GRACE CHURCH</span>
      </span>
    </div>
  </main>
</body>
</html>
```